Corvelle Meadow Organic Flower Farm, Farmer Florist

I am a flower grower and florist, so I do everything from the field to the vase. I want to include my website, phone, email and instagram

```html
<!DOCTYPE html>
<html lang="en">
<head>
<meta charset="utf-8">
<title>Corvelle Meadow – Business Cards</title>
<link rel="stylesheet" href="https://fonts.googleapis.com/css2?family=Cinzel:wght@400;500&family=Arimo:wght@400&display=swap">
<style>
  :root {
    --backdrop: #a9a9a9;
    --card-white: #ffffff;
    --maroon: #5e2b33;
    --maroon-soft: #7a4a50;
    --mint: #9bcfa3;
    --mint-pale: #e3f2e5;
    --ink-grey: #555555;
    --rule-grey: #9a9a9a;
  }
  html, body {
    margin: 0;
    padding: 0;
    width: 1200px;
    height: 1200px;
    overflow: hidden;
    background: var(--backdrop);
  }
  .canvas {
    position: relative;
    width: 1200px;
    height: 1200px;
  }
  .card {
    position: absolute;
    top: 303px;
    height: 594px;
    box-sizing: border-box;
    overflow: hidden;
  }
  .card--front {
    left: 200px;
    width: 370px;
    background: var(--mint);
  }
  .front-art {
    position: absolute;
    inset: 0;
    background:
      radial-gradient(ellipse 70% 40% at 50% 42%, var(--mint-pale) 0%, rgba(227,242,229,0) 70%),
      linear-gradient(to bottom,
        var(--mint) 0%,
        var(--mint) 28%,
        var(--mint-pale) 40%,
        var(--maroon-soft) 54%,
        var(--maroon) 64%,
        var(--maroon) 100%);
  }
  .front-art__seam {
    position: absolute;
    left: 0;
    right: 0;
    top: 418px;
    height: 1px;
    background: rgba(255,255,255,0.35);
  }
  .card--back {
    left: 599px;
    width: 364px;
    background: var(--card-white);
    text-align: center;
    color: var(--ink-grey);
  }
  .brand {
    position: absolute;
    left: 0;
    right: 0;
    top: 396px;
    top: 80px;
  }
  .brand__mark {
    display: block;
    width: 72px;
    height: 58px;
    margin: 0 auto 28px;
    background: var(--maroon);
  }
  .brand__name {
    font-family: "Cinzel", serif;
    font-weight: 400;
    font-size: 40px;
    letter-spacing: 3px;
    color: var(--maroon);
    line-height: 1;
    margin: 0;
  }
  .brand__tagline {
    font-family: "Arimo", sans-serif;
    font-size: 17px;
    color: var(--mint);
    letter-spacing: 2px;
    margin: 14px 0 0;
  }
  .brand__est {
    font-family: "Cinzel", serif;
    font-weight: 500;
    font-size: 12px;
    letter-spacing: 4px;
    color: var(--maroon);
    margin: 12px 0 0;
  }
  .person {
    position: absolute;
    left: 0;
    right: 0;
    top: 354px;
  }
  .person__name {
    font-family: "Cinzel", serif;
    font-weight: 500;
    font-size: 25px;
    color: var(--maroon);
    margin: 0;
    line-height: 1.1;
  }
  .person__role {
    font-family: "Arimo", sans-serif;
    font-size: 16px;
    margin: 2px 0 0;
  }
  .icon-row {
    position: absolute;
    left: 0;
    right: 0;
    top: 411px;
    display: flex;
    justify-content: center;
    align-items: center;
    gap: 4px;
  }
  .icon-row__rule {
    width: 52px;
    height: 1px;
    background: var(--rule-grey);
    margin: 0 4px;
  }
  .icon-box {
    width: 25px;
    height: 25px;
    border-radius: 3px;
    background: var(--maroon);
    display: flex;
    align-items: center;
    justify-content: center;
  }
  .contact {
    position: absolute;
    left: 0;
    right: 0;
    top: 446px;
    font-family: "Arimo", sans-serif;
    font-size: 16.5px;
    line-height: 22px;
    margin: 0;
  }
  .social-row {
    position: absolute;
    left: 0;
    right: 0;
    top: 524px;
    display: flex;
    justify-content: center;
    align-items: center;
  }
  .social-row__rule {
    width: 74px;
    height: 1px;
    background: var(--rule-grey);
    margin: 0 8px;
  }
  .social-dot {
    width: 32px;
    height: 32px;
    border-radius: 50%;
    background: var(--maroon);
  }
</style>
</head>
<body>
<main class="canvas">
  <section class="card card--front">
    <div class="front-art" role="img" aria-label="Illustration of a striped barn with a white roof and a small bird on the ridge against a mint sky">
      <span class="front-art__seam"></span>
    </div>
  </section>

  <section class="card card--back">
    <header class="brand">
      <span class="brand__mark" role="img" aria-label="Brand emblem area"></span>
      <h1 class="brand__name">CORVELLE</h1>
      <p class="brand__tagline">organic flower farm</p>
      <p class="brand__est">EST. 2019</p>
    </header>

    <div class="person">
      <h2 class="person__name">ELIAS MARLOW</h2>
      <p class="person__role">Managing Director</p>
    </div>

    <div class="icon-row">
      <span class="icon-row__rule"></span>
      <span class="icon-box" aria-label="Phone">
        <svg width="15" height="15" viewBox="0 0 24 24"><path fill="#fff" d="M6.6 10.8a15 15 0 0 0 6.6 6.6l2.2-2.2c.3-.3.7-.4 1-.2 1.1.4 2.3.6 3.6.6.6 0 1 .4 1 1V20c0 .6-.4 1-1 1A17 17 0 0 1 3 4c0-.6.4-1 1-1h3.5c.6 0 1 .4 1 1 0 1.3.2 2.5.6 3.6.1.3 0 .7-.2 1z"/></svg>
      </span>
      <span class="icon-box" aria-label="Email">
        <svg width="15" height="15" viewBox="0 0 24 24"><rect x="2.5" y="5.5" width="19" height="13" fill="none" stroke="#fff" stroke-width="1.8"/><path d="M2.5 5.5l9.5 7.5 9.5-7.5" fill="none" stroke="#fff" stroke-width="1.8"/></svg>
      </span>
      <span class="icon-box" aria-label="Website">
        <svg width="15" height="15" viewBox="0 0 24 24"><circle cx="12" cy="12" r="9" fill="none" stroke="#fff" stroke-width="1.8"/><ellipse cx="12" cy="12" rx="4" ry="9" fill="none" stroke="#fff" stroke-width="1.5"/><path d="M3 12h18" stroke="#fff" stroke-width="1.5"/></svg>
      </span>
      <span class="icon-row__rule"></span>
    </div>

    <p class="contact">
      044-987 654 321<br>
      hello@corvellemeadow.com<br>
      www.corvellemeadow.com
    </p>

    <div class="social-row">
      <span class="social-row__rule"></span>
      <span class="social-dot" aria-label="Social profile"></span>
      <span class="social-row__rule"></span>
    </div>
  </section>
</main>
</body>
</html>
```